One Page Website for Personal Trainer in London

I have a logo and need a one page website designed around my branding. I am a freelance Personal Trainer based in London specialising in bodyweight training for men and women. I would like the site to be modern and clean but not overtly urban in design.
I need the following headings:
About Me
My Services
Events
Blog
I don't need them to be seperate pages but if they can link to further down the page that would be great.
Industry/Entity Type
Personal Trainer
Coding
Coded - Design and coding required
Number of Pages Required
1 page
Requirements
Must have
- I need the following headings:
- About Me
- My Services
- Events
- Blog
- mobile friendly formatting
- health and fitness related photography
- Colour scheme in keeping with my existing logo

```html
<!DOCTYPE html>
<html lang="en">
<head>
<meta charset="utf-8">
<title>Harriet Vale Personal Training</title>
<link rel="stylesheet" href="https://fonts.googleapis.com/css2?family=Montserrat:wght@400;500;600&family=Open+Sans:wght@400;600;700&display=swap">
<style>
:root{
  --orange:#f7941d;
  --orange-deep:#ef8a12;
  --ink:#2b2b2b;
  --text:#333333;
  --muted:#8a8a8a;
  --rule:#9a9a9a;
  --paper:#ffffff;
  --mist:#ededed;
  --night:#252525;
  --nav:#111111;
}
*{margin:0;padding:0;box-sizing:border-box}
html,body{width:1200px;height:3468px;overflow:hidden}
body{position:relative;background:var(--paper);font-family:"Open Sans",Arial,sans-serif;color:var(--text)}
.abs{position:absolute}

/* hero */
.hero{position:absolute;left:0;top:0;width:1200px;height:793px;overflow:hidden}
.hero-photo{position:absolute;inset:0;background:
  radial-gradient(ellipse 420px 360px at 1000px 300px,rgba(210,120,110,.55),transparent 70%),
  radial-gradient(ellipse 320px 300px at 200px 300px,rgba(200,170,150,.5),transparent 70%),
  radial-gradient(ellipse 700px 260px at 600px 80px,rgba(240,220,190,.7),transparent 75%),
  linear-gradient(180deg,#bba58c 0%,#6e5b4c 45%,#2f2a29 75%,#1c1a1b 100%)}
.hero-shade{position:absolute;inset:0;background:linear-gradient(180deg,rgba(0,0,0,.05) 0%,rgba(0,0,0,.25) 55%,rgba(0,0,0,.45) 100%)}
.brand{position:absolute;left:104px;top:118px;display:flex;align-items:center;gap:10px}
.brand-dot{width:22px;height:22px;border-radius:50%;background:var(--orange)}
.brand-name{font-family:"Montserrat",Arial,sans-serif;font-weight:600;font-size:30px;color:var(--orange)}
.nav{position:absolute;left:548px;top:46px;width:700px;height:46px;border-radius:23px;background:var(--nav);display:flex;align-items:center;padding-left:82px;font-size:14px;color:#fff}
.nav a{color:#fff;text-decoration:none}
.nav a.active{color:var(--orange)}
.nav .sep{margin:0 11px;color:#fff}
.hero-kicker{position:absolute;left:0;width:1200px;top:462px;text-align:center;font-family:"Montserrat",Arial,sans-serif;font-weight:500;font-size:24px;letter-spacing:.5px;color:#fff}
.hero-title{position:absolute;left:0;width:1200px;top:480px;text-align:center;font-family:"Montserrat",Arial,sans-serif;font-weight:500;color:var(--orange);line-height:1}
.hero-title .l1{display:block;font-size:82px}
.hero-title .l2{display:block;font-size:62px;margin-top:8px}

/* section headings */
.sec-title{position:absolute;left:0;width:1200px;text-align:center;font-weight:700;font-size:42px}
.rule{position:absolute;left:116px;width:913px;height:2px;background:var(--rule)}
.rule-mark{position:absolute;left:594px;width:12px;height:12px;border-radius:50%;background:var(--orange)}
.to-top{position:absolute;left:1134px;width:46px;height:46px;border-radius:50%;background:var(--orange)}

/* about */
.about-lead{position:absolute;left:118px;top:970px;width:520px;font-weight:600;font-size:15px;line-height:20px;text-transform:uppercase;color:var(--ink)}
.about-copy{position:absolute;left:118px;top:1048px;width:518px;font-size:12.5px;line-height:20px;color:var(--muted)}
.about-copy p{margin-bottom:20px}
.about-photo{position:absolute;left:742px;top:960px;width:336px;height:405px;background:linear-gradient(180deg,#d9c8b5 0%,#b99c80 45%,#a5876d 100%)}

/* services */
.services{position:absolute;left:0;top:1461px;width:1200px;height:648px;background:var(--mist)}
.service{position:absolute;top:1658px;width:303px}
.service-photo{width:303px;height:229px}
.service h3{margin-top:30px;font-size:17px;font-weight:700;color:var(--ink)}
.service p{margin-top:8px;font-size:12px;line-height:20px;color:var(--text)}

/* blog */
.blog{position:absolute;left:0;top:2109px;width:1200px;height:608px;background:var(--orange)}
.blog .sec-title{color:#fff}
.blog .rule{background:rgba(255,255,255,.7)}
.blog .rule-mark{background:#fff}
.post{position:absolute;top:2296px;width:268px;height:328px;background:#fff;border-radius:4px;overflow:hidden}
.post-photo{height:190px}
.post-date{position:absolute;left:4px;top:4px;width:46px;height:56px;background:var(--orange);color:#fff;text-align:center}
.post-date b{display:block;font-size:24px;line-height:30px;font-weight:600}
.post-date span{display:block;font-size:9px}
.post h4{margin:18px 18px 0;font-size:16px;line-height:21px;font-weight:700;color:var(--ink)}
.post p{margin:10px 18px 0;font-size:11px;line-height:15px;color:var(--muted)}

/* events + testimonials */
.col-title{position:absolute;font-weight:700;font-size:28px;color:var(--orange)}
.col-rule{position:absolute;height:2px;background:#cfcfcf}
.arrows{position:absolute;display:flex;gap:8px}
.arrows svg{display:block}
.divider{position:absolute;left:606px;top:2790px;width:1px;height:280px;background:#e3e3e3}
.event{position:absolute;left:97px;width:470px}
.event-date{position:absolute;left:0;top:0;width:65px;height:74px}
.event-date b{display:block;height:44px;background:#3a3a3a;color:#fff;font-size:22px;font-weight:600;text-align:center;line-height:44px}
.event-date span{display:block;height:30px;background:var(--orange);color:#fff;font-size:15px;text-align:center;line-height:30px}
.event h5{position:absolute;left:95px;top:4px;font-size:16px;font-weight:600;color:var(--ink);white-space:nowrap}
.event p{position:absolute;left:95px;top:34px;width:370px;font-size:12px;line-height:18px;color:var(--text)}
.event-sep{position:absolute;left:97px;top:2959px;width:463px;height:1px;background:#dcdcdc}
.client-photo{position:absolute;left:664px;top:2860px;width:136px;height:136px;border-radius:50%;background:linear-gradient(180deg,#e6e1dc,#c9a48a);border:4px solid #f3f3f3}
.client-name{position:absolute;left:664px;top:3004px;width:136px;text-align:center;font-size:12px;font-weight:700;color:var(--orange)}
.quote{position:absolute;left:832px;top:2858px;width:294px;font-size:12px;line-height:19px;color:var(--text);text-align:justify}
.quote .mk{color:var(--orange);font-size:26px;font-weight:700;line-height:0;vertical-align:-6px}

/* footer */
.footer{position:absolute;left:0;top:3149px;width:1200px;height:319px;background:var(--night);text-align:center}
.footer .addr{position:absolute;left:0;width:1200px;top:64px;font-size:19px;font-weight:700;color:#fff}
.footer .phone{position:absolute;left:0;width:1200px;top:96px;font-size:19px;font-weight:700;color:var(--orange)}
.socials{position:absolute;left:545px;top:166px;display:flex;gap:26px}
.socials span{width:13px;height:13px;border-radius:50%;background:#fff;display:block}
.copy{position:absolute;left:0;width:1200px;top:232px;font-size:11px;color:#6d6d6d}
</style>
</head>
<body>

<header class="hero" id="home">
  <div class="hero-photo" role="img" aria-label="Photo of two women doing bodyweight exercises in a bright gym"></div>
  <div class="hero-shade"></div>
  <div class="brand"><span class="brand-dot"></span><span class="brand-name">Harriet Vale</span></div>
  <nav class="nav">
    <a class="active" href="#home">Home</a><span class="sep">|</span>
    <a href="#about">About Me</a><span class="sep">|</span>
    <a href="#services">My Services</a><span class="sep">|</span>
    <a href="#events">Events</a><span class="sep">|</span>
    <a href="#blog">Blog</a><span class="sep">|</span>
    <a href="#contact">Contact us</a>
  </nav>
  <p class="hero-kicker">I AM A FREELANCE PERSONAL TRAINER BASED IN LONDON SPECIALISING IN</p>
  <h1 class="hero-title"><span class="l1" style="margin-top:15px">Bodyweight training</span><span class="l2">for men and women.</span></h1>
</header>

<section id="about">
  <h2 class="sec-title" style="top:830px;color:var(--ink)">About us</h2>
  <div class="rule" style="top:915px"></div>
  <div class="rule-mark" style="top:910px"></div>
  <p class="about-lead">Negare non possum. Dolore malum est: in crucem qui agitur, beatus esse non potest. Quae cum dixisset paulumque institisset</p>
  <div class="about-copy">
    <p>Training with your own body weight builds strength that carries into daily life. Every session is planned around your goals, your schedule and your current level, so progress stays steady and safe. I coach clients in parks, gyms and at home across the city, with clear feedback at every step and simple routines to follow between sessions.</p>
    <p>Good movement comes first. We work on posture, balance and control before adding load, speed or volume to any exercise.</p>
    <p>Most clients train with me two or three times a week. Alongside the sessions you receive a short plan for the days in between, tips on sleep and recovery, and regular check-ins to keep you on track. Results come from steady habits, not quick fixes.</p>
  </div>
  <div class="about-photo" role="img" aria-label="Photo of the trainer standing on a beach at sunset"></div>
  <div class="to-top" style="top:1438px"></div>
</section>

<section class="services" id="services"></section>
<h2 class="sec-title" style="top:1520px;color:var(--ink)">Our Service</h2>
<div class="rule" style="top:1594px"></div>
<div class="rule-mark" style="top:1589px"></div>
<article class="service" style="left:122px">
  <div class="service-photo" role="img" aria-label="Photo of a woman stretching in a lunge by the sea" style="background:linear-gradient(180deg,#c9d8e6 0%,#9fb6cc 55%,#7c8b98 100%)"></div>
  <h3>Stretching</h3>
  <p>Gentle, guided stretching routines that improve mobility, ease tension and help your body recover between harder sessions. Suitable for every level and easy to repeat at home.</p>
</article>
<article class="service" style="left:462px">
  <div class="service-photo" role="img" aria-label="Photo of a woman exercising with light dumbbells" style="background:linear-gradient(135deg,#e8c86a 0%,#6f8aa0 50%,#2f4a63 100%)"></div>
  <h3>Bodyweight Excercise</h3>
  <p>Push, pull, squat and core work using nothing but your own body. Sessions build real strength and stamina, and every move scales up as you get fitter.</p>
</article>
<article class="service" style="left:800px">
  <div class="service-photo" role="img" aria-label="Photo of trainers, dumbbells, a towel and a skipping rope on a wooden floor" style="background:linear-gradient(135deg,#7e7a76 0%,#5a5d63 50%,#3e3f44 100%)"></div>
  <h3>Fitness Plans</h3>
  <p>A clear weekly plan written for your goals, with workouts, rest days and simple food advice. Plans are reviewed each month so they grow with your progress.</p>
</article>
<div class="to-top" style="top:2053px"></div>

<section class="blog" id="blog">
  <h2 class="sec-title" style="top:80px">Latest Blog</h2>
  <div class="rule" style="top:137px"></div>
  <div class="rule-mark" style="top:132px"></div>
</section>
<article class="post" style="left:42px">
  <div class="post-photo" role="img" aria-label="Photo of a woman in a plank position" style="background:linear-gradient(135deg,#d9b7a4,#4f8e9a 60%,#2d5660)"></div>
  <div class="post-date"><b>22</b><span>October</span></div>
  <h4>Negare non possum. Dolore malum est</h4>
  <p>Five simple moves to wake up your body before a busy working day.</p>
</article>
<article class="post" style="left:326px">
  <div class="post-photo" role="img" aria-label="Photo of a couple jogging outdoors" style="background:linear-gradient(135deg,#cfd3c4,#9b9a86 55%,#5c5a4e)"></div>
  <div class="post-date"><b>23</b><span>October</span></div>
  <h4>Quod autem satis est, eo quic uid accessit</h4>
  <p>How running with a partner keeps you training through the colder months.</p>
</article>
<article class="post" style="left:608px">
  <div class="post-photo" role="img" aria-label="Photo of women in a group fitness class with dumbbells" style="background:linear-gradient(135deg,#cfe4d8,#9ccbbf 50%,#5b9a8c)"></div>
  <div class="post-date"><b>24</b><span>October</span></div>
  <h4>Alios in primisque familiarem nostrum Posidonium</h4>
  <p>Why short group classes are a great way to start a new routine.</p>
</article>
<article class="post" style="left:892px">
  <div class="post-photo" role="img" aria-label="Photo of a woman stretching on grass at sunset" style="background:linear-gradient(135deg,#e9d6a4,#b7a36c 50%,#6f6a44)"></div>
  <div class="post-date"><b>24</b><span>October</span></div>
  <h4>Vicimus. Hanc ergo intuens debet institutum</h4>
  <p>Evening stretches that help you relax and sleep better after training.</p>
</article>

<section id="events">
  <h3 class="col-title" style="left:92px;top:2776px">Events</h3>
  <div class="arrows" style="left:512px;top:2787px">
    <svg width="18" height="18" viewBox="0 0 18 18"><circle cx="9" cy="9" r="9" fill="#f7941d"/><path d="M10.5 5 6.5 9l4 4" stroke="#fff" stroke-width="2" fill="none"/></svg>
    <svg width="18" height="18" viewBox="0 0 18 18"><circle cx="9" cy="9" r="9" fill="#f7941d"/><path d="M7.5 5l4 4-4 4" stroke="#fff" stroke-width="2" fill="none"/></svg>
  </div>
  <div class="col-rule" style="left:92px;top:2835px;width:468px"></div>
  <div class="event" style="top:2870px">
    <div class="event-date"><b>30</b><span>Oct</span></div>
    <h5>Verum tamen cum de rebus</h5>
    <p>Outdoor bootcamp in the park, open to all levels. Bring water and a mat.</p>
  </div>
  <div class="event-sep"></div>
  <div class="event" style="top:2984px">
    <div class="event-date"><b>31</b><span>Oct</span></div>
    <h5>Verum tamen cum de rebus</h5>
    <p>Evening mobility workshop with a relaxed pace. Places are limited, book early.</p>
  </div>
</section>

<div class="divider"></div>

<section id="testimonials">
  <h3 class="col-title" style="left:661px;top:2776px">Testimonials</h3>
  <div class="arrows" style="left:1076px;top:2787px">
    <svg width="18" height="18" viewBox="0 0 18 18"><circle cx="9" cy="9" r="9" fill="#f7941d"/><path d="M10.5 5 6.5 9l4 4" stroke="#fff" stroke-width="2" fill="none"/></svg>
    <svg width="18" height="18" viewBox="0 0 18 18"><circle cx="9" cy="9" r="9" fill="#f7941d"/><path d="M7.5 5l4 4-4 4" stroke="#fff" stroke-width="2" fill="none"/></svg>
  </div>
  <div class="col-rule" style="left:661px;top:2835px;width:463px"></div>
  <div class="client-photo" role="img" aria-label="Round portrait photo of a smiling client"></div>
  <div class="client-name">CLARA</div>
  <p class="quote"><span class="mk">&ldquo;</span> Training with Harriet changed the way I think about exercise. After three months I feel stronger, sleep better and actually enjoy every session. The plans are clear, the workouts fit my week, and I never feel rushed. I would recommend her to anyone starting out. <span class="mk">&rdquo;</span></p>
</section>

<footer class="footer" id="contact">
  <p class="addr">2140 Linden Row, Bramford, Kent 55120</p>
  <p class="phone">Phone (555) 014 2290</p>
  <div class="socials" aria-label="Social links"><span></span><span></span><span></span><span></span></div>
  <p class="copy">&copy; 2017 All rights reserved by Harriet Vale</p>
</footer>

</body>
</html>
```